Brief 1.
An Overview / Background of the Business & Services-
It is a new business being set up. Our business is to design a solution to enable Alumni of higher institutions in Nigeria apply for their academic transcript through our system. the name of our product will be Record Relay Nigeria. We need logo, site banner, advert banner and several academic images. See www.rrly-ng.example for more insight.
The Target Market / Audience you are trying to reach-
Alumni of Nigeria Universities, usually between the ages of 20-40.
Design Specifics; any preferences or ideas for Style, Colour, Imagery, etc-
Color scheme will be several shades of light blue and white. Please check www.rrly-ng.example for more insight.

Brief 2

Pantrybasket.com is an online food and grocery shop, we supply fresh food stuff and other daily essential needs on request to customers. The site is already up (www.pantrybasket.example). We need logo, site rolling banner, advert banner and several offer graphics as shown in the placeholder images in the site now.
Working women in Nigeria.
Color scheme will be several shades of light Green and White. Please check the site.

```html
<!DOCTYPE html>
<html lang="en">
<head>
<meta charset="utf-8">
<title>Pantrybasket – Home</title>
<link href="https://fonts.googleapis.com/css2?family=Arimo:wght@400;700&family=Rubik:wght@300;800;900&display=swap" rel="stylesheet">
<style>
:root{
  --green:#4f9a12;
  --green-dark:#3d7f0b;
  --green-light:#6bb82a;
  --orange:#f06a10;
  --orange-soft:#f8b060;
  --ink:#333;
  --muted:#666;
  --line:#d9d9d9;
  --nav:#d5d5d5;
  --nav-dark:#2b2b2b;
  --bg:#fff;
}
*{box-sizing:border-box;margin:0;padding:0}
html,body{width:818px;height:1200px;overflow:hidden;background:var(--bg)}
body{position:relative;font-family:Arimo,Arial,sans-serif;color:var(--ink);font-size:8px}
.abs{position:absolute}
.brand{display:flex;align-items:center;gap:7px;color:var(--green);font-weight:700;font-size:19px;letter-spacing:.5px}
.brand-dot{width:28px;height:28px;border-radius:50%;background:var(--green-light)}
.top-links{left:354px;top:26px;display:flex;gap:22px;font-size:7.5px;color:#444}
.welcome{left:378px;top:55px;font-size:7.5px;font-style:italic;color:var(--green-dark)}
.search{left:565px;top:50px;width:137px;height:18px;border:1px solid var(--line);font-size:6.5px;color:#777;padding:5px 7px}
.search svg{position:absolute;right:5px;top:4px}
.nav{left:118px;top:84px;width:584px;height:26px;background:linear-gradient(#e4e4e4,#cfcfcf);display:flex;font-size:7px;color:#444;align-items:center}
.nav span{padding:0 16.5px}
.nav .home{background:linear-gradient(#444,#1e1e1e);color:#fff;height:100%;display:flex;align-items:center;padding:0 23px}
.promo{top:119px;height:58px;border:1px solid var(--line);display:flex;align-items:center}
.promo h2{font-family:Rubik,sans-serif;font-weight:900;color:var(--green);font-size:18px;letter-spacing:.5px;line-height:1}
.promo p{font-family:Rubik,sans-serif;font-weight:800;color:var(--orange);font-size:8.5px;margin-top:5px;letter-spacing:.3px}
.photo{display:block}
.hero-text{left:139px;top:313px}
.hero-text b{display:block;font-family:Rubik,sans-serif;font-weight:900;font-size:16px;color:var(--green-dark);letter-spacing:.5px}
.hero-text span{display:block;font-family:Rubik,sans-serif;font-weight:300;font-size:24px;color:#333;margin-top:2px}
.slider-arrows{left:481px;top:384px;display:flex;gap:1px}
.slider-arrows i{width:16px;height:16px;background:rgba(90,90,90,.6);display:block;color:#fff;font-style:normal;text-align:center;line-height:16px;font-size:9px}
.offer{left:526px;top:186px;width:176px;height:106px;background:linear-gradient(135deg,var(--orange-soft),#f7983a);text-align:center;color:#fff}
.offer h3{font-family:Rubik,sans-serif;font-weight:900;font-size:11px;margin-top:19px;line-height:1.5;letter-spacing:.6px}
.offer p{font-size:11px;margin-top:4px;font-weight:400}
.offer .btn{display:inline-block;margin-top:7px;background:#ddd;color:#555;font-size:7.5px;padding:6px 20px}
.herbal{left:526px;top:298px;width:176px;height:106px;background:linear-gradient(90deg,#fff 30%,#eccab2 60%,#f5e6dc)}
.herbal-text{left:540px;top:312px;font-family:Rubik,sans-serif;font-weight:900;font-size:10.5px;line-height:1.4;color:#222}
.herbal-text em{display:block;font-style:normal;color:var(--green-dark)}
.herbal-text small{display:block;color:var(--orange);font-size:7.5px}
.section-title{font-size:9.5px;color:var(--green);font-weight:400;letter-spacing:.2px}
.arrows{font-size:8px;color:#aaa;letter-spacing:4px}
.cats{left:118px;top:438px;width:137px}
.cats li{list-style:none;height:21px;border-bottom:1px solid #fff;background:linear-gradient(#f2f2f2,#e6e6e6);display:flex;align-items:center;padding:0 10px;font-size:7px;color:#444;justify-content:space-between}
.cats li .plus{width:7px;height:7px;border:1px solid #999;font-size:6px;line-height:5px;text-align:center;color:#777}
.hurry{left:118px;top:578px;width:137px;height:219px;background:linear-gradient(180deg,#2a0d12 0%,#3a0f18 45%,#b01e3c 75%,#e8708a 100%)}
.hurry-text{left:118px;top:601px;width:137px;text-align:center;font-family:Rubik,sans-serif;font-weight:900;color:var(--orange);font-size:11.5px;line-height:1.25}
.hurry-pct{left:133px;top:636px;font-family:Rubik,sans-serif;font-weight:900;color:#ffd21a;font-size:32px}
.hurry-pct small{font-size:9.5px;color:#fff}
.special{left:118px;top:813px;width:137px;height:165px;border:1px solid var(--line)}
.card{width:129px;height:159px;border:1px solid var(--line);text-align:center}
.card .img{position:absolute;left:8px;top:8px;width:111px;height:90px;border-radius:4px}
.card h4{position:absolute;top:118px;width:100%;font-size:8.5px;font-weight:400;color:var(--green)}
.card .price{position:absolute;left:12px;top:139px;font-size:9px;color:var(--green-dark)}
.card .cart{position:absolute;left:59px;top:134px;width:59px;height:15px;border:1px solid #aaa;background:linear-gradient(#fafafa,#ddd);font-size:5.5px;color:#444;line-height:13px}
.card.active .band{position:absolute;left:-1px;top:110px;width:129px;height:52px;background:var(--green)}
.card.active h4,.card.active .price{color:#fff}
.footer{left:0;top:1012px;width:818px;height:188px;background:linear-gradient(#ececec,#fff 30px)}
.fcol h5{font-size:8px;color:var(--green);font-weight:700;margin-bottom:7px}
.fcol li{list-style:none;font-size:6.5px;color:#555;height:16.4px}
.social{display:flex;align-items:center;gap:5px;font-size:6.5px;color:#555;margin-bottom:14px}
.social i{width:19px;height:19px;border-radius:50%;background:#666;display:block}
.pay{left:561px;top:1054px;width:140px;height:26px;border:1px solid #ccc;background:#f4f4f4;display:flex;gap:3px;padding:5px}
.pay i{flex:1;background:#fff;border:1px solid #bbb;display:block}
.copyright{left:0;top:1158px;width:818px;text-align:center;font-size:6.5px;color:#555}
</style>
</head>
<body>

<header>
  <div class="abs brand" style="left:120px;top:30px"><span class="brand-dot"></span>PANTRYBASKET</div>
  <nav class="abs top-links"><span>My Account</span><span>My Wishlist</span><span>My Cart</span><span>Checkout</span><span>Log In</span><span>&#128722; Your cart is : 0 items</span></nav>
  <p class="abs welcome">Welcome to Pantrybasket.com. Feed well, live well</p>
  <div class="abs search">Search :
    <svg width="10" height="10" viewBox="0 0 10 10"><circle cx="4" cy="4" r="3" fill="none" stroke="#888" stroke-width="1.2"/><line x1="6.3" y1="6.3" x2="9" y2="9" stroke="#888" stroke-width="1.4"/></svg>
  </div>
  <nav class="abs nav"><span class="home">HOME</span><span>HEALTH &amp; WELLNESS</span><span>FRUITS &amp; VEGS</span><span>POULTRY, MEAT &amp; FISH</span><span>FOOD STUFFS</span><span>RECIPES</span><span>OTHERS</span></nav>
</header>

<section>
  <div class="abs promo" style="left:118px;width:288px">
    <svg style="margin:0 20px 0 20px" width="44" height="26" viewBox="0 0 44 26"><rect x="12" y="2" width="31" height="17" fill="#888"/><path d="M1 10 L5 5 H12 V19 H1Z" fill="#777"/><circle cx="8" cy="21" r="4" fill="#fff" stroke="#777" stroke-width="2"/><circle cx="34" cy="21" r="4" fill="#fff" stroke="#777" stroke-width="2"/></svg>
    <div><h2>FREE SHIPPING</h2><p>ON ORDER OVER $30 OFFER TODAY</p></div>
  </div>
  <div class="abs promo" style="left:414px;width:288px">
    <svg style="margin:0 23px 0 20px" width="40" height="40" viewBox="0 0 40 40"><circle cx="20" cy="20" r="18" fill="none" stroke="#777" stroke-width="2"/><path d="M14 11c-2 2-2 6 1 11s7 8 10 8l3-3-4-4-2 2c-2-1-5-4-6-6l2-2-4-4z" fill="#777"/></svg>
    <div><h2>GIVE US CALL</h2><p>1-800 PANTRY (1-800-555-0142)</p></div>
  </div>

  <div class="abs photo" role="img" aria-label="Smiling woman eating a fresh salad" style="left:118px;top:186px;width:401px;height:218px;background:linear-gradient(90deg,#b9d6e0 0%,#d9e4e6 35%,#d8b7a0 60%,#c7967a 100%)"></div>
  <div class="abs hero-text"><b>HEALTHY WELLNESS</b><span>&amp; VIEW MORE PRODUCTS</span></div>
  <div class="abs slider-arrows"><i>&#8249;</i><i>&#8250;</i></div>

  <div class="abs offer"><h3>FREE DELIVERY &amp;<br>GET 10% DISCOUNT</h3><p>on every Registered Users</p><span class="btn">READ MORE</span></div>
  <div class="abs herbal" role="img" aria-label="Relaxed legs for spa products"></div>
  <div class="abs herbal-text"><em>HERBAL &amp;</em>AYURVEDIC<small>&amp; SPA PRODUCTS</small></div>
</section>

<aside>
  <h3 class="abs section-title" style="left:118px;top:420px">CATEGORIES</h3>
  <ul class="abs cats">
    <li><span>&#8250;&nbsp; Health &amp; Wellness</span></li>
    <li><span>&#8250;&nbsp; Fruits &amp; Vegs</span><span class="plus">+</span></li>
    <li><span>&#8250;&nbsp; Poultry, Meat &amp; Fish</span><span class="plus">+</span></li>
    <li><span>&#8250;&nbsp; Food Stuffs</span><span class="plus">+</span></li>
    <li><span>&#8250;&nbsp; Recipes</span></li>
    <li><span>&#8250;&nbsp; Others</span><span class="plus">+</span></li>
  </ul>
  <div class="abs hurry" role="img" aria-label="Strawberries splashing in cream"></div>
  <div class="abs hurry-text">HURRY OFFER<br>ENDS SOON</div>
  <div class="abs hurry-pct">50%<small>OFFER</small></div>

  <div class="abs special">
    <h3 class="abs section-title" style="left:11px;top:16px">SPECIAL PRODUCTS</h3>
    <span class="abs arrows" style="left:114px;top:16px">&#8249;&#8250;</span>
    <div class="abs" role="img" aria-label="Red, green and yellow bell peppers" style="left:14px;top:34px;width:108px;height:76px;border-radius:8px;background:linear-gradient(90deg,#d8322a,#3d7a22 50%,#f1a91e)"></div>
    <p class="abs" style="left:15px;top:120px;font-size:9px;color:var(--green)">CUM SOCIIS</p>
    <p class="abs" style="left:14px;top:141px;font-size:9px;color:var(--green-dark)">130.00</p>
    <span class="abs" style="left:58px;top:135px;width:67px;height:18px;background:var(--orange);color:#fff;font-size:6.5px;text-align:center;line-height:18px">ADD TO CART</span>
  </div>
</aside>

<main>
  <h3 class="abs section-title" style="left:282px;top:420px">LATEST PRODUCTS</h3>
  <span class="abs arrows" style="left:686px;top:420px">&#8249;&#8250;</span>

  <div class="abs card active" style="left:282px;top:441px"><div class="band"></div><div class="img" role="img" aria-label="Whole fresh fish" style="background:linear-gradient(#fff 30%,#8c8a74 50%,#fff 70%)"></div><h4>TILAPIA FISH (1KG)</h4><span class="price" style="top:141px">1,000.00</span><span class="cart" style="top:136px">ADD TO CART</span></div>
  <div class="abs card" style="left:427px;top:441px"><div class="img" role="img" aria-label="Pasta, tomatoes and olive oil" style="background:radial-gradient(circle,#e8c24a,#b84026 50%,#fff 72%)"></div><h4>TILAPIA FISH (1KG)</h4><span class="price">1,000.00</span><span class="cart">ADD TO CART</span></div>
  <div class="abs card" style="left:573px;top:441px"><div class="img" role="img" aria-label="Sacks of nuts and vegetables" style="background:radial-gradient(circle,#c98a4e,#e7c9a0 50%,#fff 75%)"></div><h4>TILAPIA FISH (1KG)</h4><span class="price">1,000.00</span><span class="cart">ADD TO CART</span></div>

  <h3 class="abs section-title" style="left:282px;top:621px">FEATURED PRODUCTS</h3>
  <span class="abs arrows" style="left:686px;top:621px">&#8249;&#8250;</span>

  <div class="abs card" style="left:282px;top:642px"><div class="img" role="img" aria-label="Silver fish" style="background:linear-gradient(#fff 35%,#9a9a88 50%,#fff 65%)"></div><h4>TILAPIA FISH (1KG)</h4><span class="price">1,000.00</span><span class="cart">ADD TO CART</span></div>
  <div class="abs card" style="left:427px;top:642px"><div class="img" role="img" aria-label="Ripe peaches" style="background:radial-gradient(circle,#f5a233,#d9361f 45%,#fff 72%)"></div><h4>TILAPIA FISH (1KG)</h4><span class="price">1,000.00</span><span class="cart">ADD TO CART</span></div>
  <div class="abs card" style="left:573px;top:642px"><div class="img" role="img" aria-label="Tilapia fish" style="background:radial-gradient(ellipse,#4e5a62,#8a959a 40%,#fff 70%)"></div><h4>TILAPIA FISH (1KG)</h4><span class="price">1,000.00</span><span class="cart">ADD TO CART</span></div>

  <div class="abs card" style="left:282px;top:817px"><div class="img" role="img" aria-label="Fresh tomatoes" style="background:radial-gradient(circle,#e83a22,#c8201a 45%,#fff 72%)"></div><h4>TILAPIA FISH (1KG)</h4><span class="price">1,000.00</span><span class="cart">ADD TO CART</span></div>
  <div class="abs card" style="left:427px;top:817px"><div class="img" role="img" aria-label="Green pea pods" style="background:linear-gradient(160deg,#8ccc2a,#5a9e12 60%,#fff)"></div><h4>TILAPIA FISH (1KG)</h4><span class="price">1,000.00</span><span class="cart">ADD TO CART</span></div>
  <div class="abs card" style="left:573px;top:817px"><div class="img" role="img" aria-label="Grocery bag with fruit and vegetables" style="background:radial-gradient(circle,#c9a277,#d9503a 45%,#fff 75%)"></div><h4>TILAPIA FISH (1KG)</h4><span class="price">1,000.00</span><span class="cart">ADD TO CART</span></div>
</main>

<footer>
  <div class="abs footer"></div>
  <div class="abs" style="left:152px;top:1040px;width:36px;height:36px;border-radius:50%;background:var(--green-light)"></div>
  <div class="abs" style="left:124px;top:1084px;font-size:12px;font-weight:700;color:var(--green)">PANTRYBASKET</div>
  <div class="abs fcol" style="left:246px;top:1036px"><h5>CUSTOMER SERVICE</h5><ul><li>About Us</li><li>Delivery Information</li><li>Privacy Policy</li><li>Term &amp; Condition</li></ul></div>
  <div class="abs fcol" style="left:369px;top:1036px"><h5>MY ACCOUNT</h5><ul><li>My Product</li><li>My Orders</li><li>My Address</li><li>My Personal Info</li></ul></div>
  <div class="abs fcol" style="left:469px;top:1036px"><h5>FOLLOW US</h5><div class="social"><i></i>: Friendbook</div><div class="social"><i></i>: Chirper</div></div>
  <div class="abs fcol" style="left:561px;top:1037px"><h5>PAYMENT OPTIONS</h5></div>
  <div class="abs pay"><i></i><i></i><i></i><i></i></div>
  <div class="abs" style="left:118px;top:1142px;width:584px;height:1px;background:var(--line)"></div>
  <p class="abs copyright">© 2014 Pantrybasket. All Rights Reserved.</p>
</footer>

</body>
</html>
```